TWPC Business Card Design

Business card for sole operator professional civil and traffic engineer.
Clients are developers and planners who require assistance with traffic strategic master planning advice and design development for access and infrastructure associated with the development.
Colours already in use are greens for the business name and black for other legend. The attached file shows the letterhead template which is currently in use.
Target Market(s)
Professional Clients in development industry
Most clients known to the Principal and card is mostly required to allow ongoing contact
Industry/Entity Type
Business
Contact Information for Business Card
LACHLAN PETTIGREW CONSULTING PARTNERS
ABN 37 814 529 106
PO Box 418 KELWOOD NSW 2619
Lachlan Pettigrew 0412 358 971
l.pettigrew@corvanmail.net

```html
<!DOCTYPE html>
<html lang="en">
<head>
<meta charset="utf-8">
<title>Lachlan Pettigrew Consulting Partners – Business Card</title>
<link rel="stylesheet" href="https://fonts.googleapis.com/css2?family=Arimo:wght@400&display=swap">
<style>
  :root {
    --page-bg: #f2f2f2;
    --card-top: #ffffff;
    --card-mid: #d6e9ae;
    --card-bottom: #9cc93c;
    --ink: #111111;
  }
  * { margin: 0; padding: 0; box-sizing: border-box; }
  html, body {
    width: 1200px;
    height: 864px;
    overflow: hidden;
    background: var(--page-bg);
    font-family: "Arimo", Arial, sans-serif;
    color: var(--ink);
  }
  .business-card {
    position: absolute;
    left: 100px;
    top: 126px;
    width: 1000px;
    height: 612px;
    background: linear-gradient(to bottom, var(--card-top) 0%, var(--card-top) 14%, var(--card-mid) 48%, var(--card-bottom) 100%);
    box-shadow: 0 10px 30px rgba(0,0,0,0.18);
  }
  .company-block {
    position: absolute;
    top: 88px;
    left: 0;
    width: 100%;
    text-align: center;
  }
  .company-name {
    font-size: 34px;
    letter-spacing: 0.2px;
    line-height: 1;
  }
  .company-abn {
    font-size: 20px;
    line-height: 1;
    margin-top: 4px;
    margin-left: 40px;
  }
  .divider {
    position: absolute;
    left: 488px;
    top: 350px;
    width: 2px;
    height: 212px;
    background: var(--ink);
  }
  .person-name {
    position: absolute;
    left: 0;
    width: 488px;
    top: 462px;
    text-align: center;
    font-size: 29px;
  }
  .contact-list {
    position: absolute;
    right: 90px;
    top: 370px;
    list-style: none;
    text-align: right;
    font-size: 21px;
    line-height: 30px;
  }
  .contact-item { position: relative; padding-right: 4px; }
  .contact-icon {
    position: absolute;
    right: -30px;
    top: 7px;
    width: 16px;
    height: 16px;
    fill: var(--ink);
  }
</style>
</head>
<body>
  <div class="business-card">
    <header class="company-block">
      <h1 class="company-name" style="font-weight:400">LACHLAN PETTIGREW CONSULTING PARTNERS</h1>
      <p class="company-abn">ABN 37 814 529 106</p>
    </header>

    <p class="person-name">Lachlan Pettigrew</p>

    <div class="divider"></div>

    <ul class="contact-list">
      <li class="contact-item">0412 358 971
        <svg class="contact-icon" viewBox="0 0 16 16" aria-hidden="true">
          <path d="M2 5c0-2 2-3 6-3s6 1 6 3v1h-3V5H5v1H2z"/>
          <path d="M4 7h8l2 6H2z"/>
        </svg>
      </li>
      <li class="contact-item">PO Box 418 KELWOOD NSW 2619
        <svg class="contact-icon" viewBox="0 0 16 16" aria-hidden="true">
          <path d="M8 0a5 5 0 0 0-5 5c0 4 5 11 5 11s5-7 5-11a5 5 0 0 0-5-5zm0 7a2 2 0 1 1 0-4 2 2 0 0 1 0 4z"/>
        </svg>
      </li>
      <li class="contact-item">l.pettigrew@corvanmail.net
        <svg class="contact-icon" viewBox="0 0 16 16" aria-hidden="true">
          <path d="M1 3h14v1L8 9 1 4z"/>
          <path d="M1 6l7 5 7-5v7H1z"/>
        </svg>
      </li>
    </ul>
  </div>
</body>
</html>
```